Laser Tattoo Removal Business Cards

We are looking for a professional business card design for a laser tattoo removal business. Ideally looking for a black business card design. The name of the business is Brightline Tattoo Removal. We place our cards at local tattoo shops so we ideally are looking for something trendy/edgy to draw both male and female clientele in.

Target Market(s)

Male/Female ages 18-60

Contact Information for Business Card

black background ideally.. hoping to stay within greys, whites and black

Font styles to use
Serif
Sans Serif

Colors
121212
a9a9a9
5c5c5c
f5f5f5
ffffff
7f7f7f
606060
848484
9d9d9d

Requirements
Must have
• Employee Info:
• Melissa Thornbury
• Chief Executive Offer
• m: 919.537.2846
• w: 919.362.4178
• f: 919.685.3907
• mthornbury@brightlinetattooremoval.example
• Address:
• 4615 Oakmere Pkwy, Suite 210
• Raleigh, NC 27654
• Website:
• www.brightlinetattooremoval.example
Nice to have
• Myabe business name on back or logo on back and employee info on the front

```html
<!DOCTYPE html>
<html lang="en">
<head>
<meta charset="utf-8">
<title>Brightline Tattoo Removal – Business Cards</title>
<link rel="stylesheet" href="https://fonts.googleapis.com/css2?family=Josefin+Sans:wght@400&family=Lato:wght@700&display=swap">
<style>
  :root {
    --backdrop: #2b2b2b;
    --card: #1c1c1c;
    --ink: #f5f5f5;
    --ink-soft: #d6d6d6;
    --rule: #5c5c5c;
  }
  html, body {
    margin: 0;
    width: 1200px;
    height: 1108px;
    overflow: hidden;
    background: var(--backdrop);
  }
  .canvas {
    position: relative;
    width: 1200px;
    height: 1108px;
  }
  .card {
    position: absolute;
    top: 224px;
    width: 400px;
    height: 660px;
    background: var(--card);
    border-radius: 22px;
    box-shadow: 0 18px 40px rgba(0,0,0,0.45);
    color: var(--ink);
    text-align: center;
    box-sizing: border-box;
  }
  .card--front { left: 170px; }
  .card--back  { left: 630px; }

  .brand {
    font-family: "Josefin Sans", sans-serif;
    font-weight: 400;
    color: var(--ink);
    letter-spacing: 0.08em;
    text-transform: uppercase;
    line-height: 1.25;
    font-size: 26px;
    margin: 0;
  }
  .card--front .brand { padding-top: 72px; }
  .card--back .brand {
    position: absolute;
    top: 270px;
    left: 0;
    right: 0;
  }

  .person {
    margin-top: 66px;
    font-family: Arial, Helvetica, sans-serif;
  }
  .person__name {
    font-family: "Lato", sans-serif;
    font-weight: 700;
    font-size: 24px;
    letter-spacing: 0.02em;
    text-transform: uppercase;
    margin: 0;
  }
  .person__title {
    font-size: 18px;
    color: var(--ink-soft);
    margin: 2px 0 0;
  }
  .rule {
    width: 220px;
    height: 1px;
    background: var(--rule);
    margin: 14px auto;
    border: 0;
  }
  .contact {
    list-style: none;
    margin: 0;
    padding: 0;
    font-family: Arial, Helvetica, sans-serif;
    font-size: 19px;
    line-height: 1.35;
  }
  .contact b { font-weight: 700; }
  .contact__email { font-size: 16px; }
  .address {
    font-family: Arial, Helvetica, sans-serif;
    font-style: normal;
    font-size: 19px;
    line-height: 1.3;
  }
  .website {
    position: absolute;
    bottom: 70px;
    left: 0;
    right: 0;
    font-family: Arial, Helvetica, sans-serif;
    font-size: 17px;
    color: var(--ink-soft);
    margin: 0;
  }
</style>
</head>
<body>
<main class="canvas">
  <section class="card card--front" aria-label="Card front">
    <p class="brand">Brightline<br>Tattoo Removal</p>
    <div class="person">
      <p class="person__name">Melissa Thornbury</p>
      <p class="person__title">Chief Executive Officer</p>
    </div>
    <hr class="rule">
    <ul class="contact">
      <li><b>M:</b> 919.537.2846</li>
      <li><b>W:</b> 919.362.4178</li>
      <li><b>F:</b> 919.685.3907</li>
      <li class="contact__email"><b>E:</b> mthornbury@brightlinetattooremoval.example</li>
    </ul>
    <hr class="rule">
    <address class="address">4615 Oakmere Pkwy, Suite 210<br>Raleigh, NC 27654</address>
  </section>

  <section class="card card--back" aria-label="Card back">
    <p class="brand">Brightline<br>Tattoo Removal</p>
    <p class="website">www.brightlinetattooremoval.example</p>
  </section>
</main>
</body>
</html>
```